Velmora Consulting Business

** Please add the content information from my old business card
1. I would like to see a two sided business card with both options with the 1st Option--Tallow Spire-new WHITE BACKGROUND LOGO
2 nd Option-Tallow Spire - new BLACK- Background Logo
3rd -Option a business card with my Photo on the card
Please add the new word to the card information:
EXECUTION
AS THE OWNER'S REP
WE AIM TO ACHIEVE YOUR
INFRASTRUCTURE VISION with
OUR SPECIALIZATION & EXECUTION in:

FUNDING Planning
BUSINESS Planning
INFRASTRUCTURE Planning
PROJECT Management
Since 2012
_____________________________________________________________________
I want to get spot uv raised printing. I was liking a a nice rich white linen paper stock with black writing & NOT A COLORED CARD other than a variety of white or black cards concept

```html
<!DOCTYPE html>
<html lang="en">
<head>
<meta charset="utf-8">
<title>Velmora Consulting – Business Card</title>
<link rel="stylesheet" href="https://fonts.googleapis.com/css2?family=Arimo:wght@400;700&display=swap">
<style>
:root{
  --backdrop:#1b1b1b;
  --paper:#f3f3f3;
  --ink:#262626;
  --red:#dd1f36;
  --charcoal:#2a2a2c;
  --charcoal-dark:#222224;
  --mute:#5a5a5c;
  --white:#ffffff;
}
*{margin:0;padding:0;box-sizing:border-box}
html,body{width:1200px;height:1059px;overflow:hidden}
body{background:var(--backdrop);font-family:"Arimo",Arial,sans-serif;position:relative}
.card{position:absolute;left:256px;width:690px;height:392px;overflow:hidden;box-shadow:0 10px 30px rgba(0,0,0,.6)}
.card-front{top:89px;background:var(--paper);color:var(--ink)}
.card-back{top:546px;background:linear-gradient(90deg,var(--charcoal-dark),var(--charcoal) 50%,var(--charcoal-dark));color:var(--white);text-align:center}

.brand{position:absolute;left:40px;top:112px;display:flex;align-items:center;gap:10px}
.brand-mark{width:14px;height:14px;background:var(--red)}
.brand-name{font-size:34px;font-weight:700;color:var(--ink);letter-spacing:-.5px}

.name-tab{position:absolute;left:0;top:219px;width:22px;height:42px;background:var(--red);border-radius:0 4px 4px 0}
.person-name{position:absolute;left:40px;top:216px;font-size:24px;font-weight:700;color:var(--red)}
.person-title{position:absolute;left:40px;top:248px;font-size:16px;color:var(--ink)}

.contact-list{position:absolute;left:40px;top:286px;list-style:none}
.contact-list li{display:flex;align-items:center;gap:8px;height:25.5px;font-size:16.5px}
.contact-list svg{width:13px;height:13px;fill:var(--red);flex:none}

.front-footer{position:absolute;left:0;bottom:0;width:690px;height:40px}
.locations{position:absolute;right:38px;bottom:10px;font-size:16px;color:var(--white)}

.back-brand{position:absolute;left:0;right:0;top:70px;display:flex;justify-content:center;align-items:center;gap:12px}
.back-brand .brand-mark{background:#6a6a6c}
.back-brand .brand-name{color:#6a6a6c;font-size:46px}

.tagline{position:absolute;left:0;right:0;top:163px;font-size:18.5px;line-height:30.5px}
.tagline .lead{color:var(--red)}
.rule{position:absolute;left:0;width:100%;height:1.5px;background:var(--red)}
.rule-top{top:258px}
.rule-bottom{top:355px}
.services{position:absolute;left:0;right:0;top:272px;font-size:18.5px;line-height:32px}
.services .sep{color:var(--red);margin:0 6px}
.since{position:absolute;left:50%;top:342px;transform:translateX(-50%);padding:2px 9px;font-size:18.5px;line-height:20px;border:1.5px solid var(--red);border-radius:14px;background:var(--charcoal)}
</style>
</head>
<body>

<section class="card card-front" aria-label="Business card front">
  <div class="brand">
    <span class="brand-mark"></span>
    <span class="brand-name">Velmora Consulting</span>
  </div>

  <span class="name-tab"></span>
  <h1 class="person-name">Renata Halloway-Brisk</h1>
  <p class="person-title">CEO / LEAD PROJECT MANAGER</p>

  <ul class="contact-list">
    <li><svg viewBox="0 0 16 16"><path d="M1 5c0-2 3-3 7-3s7 1 7 3v1h-4V5H5v1H1zM3 7h10l1 7H2z"/></svg>555.014.2287</li>
    <li><svg viewBox="0 0 16 16"><path d="M1 6l7-5 7 5v9H1zM2.5 7l5.5 4 5.5-4"/></svg>renata@velmora.ca</li>
    <li><svg viewBox="0 0 16 16"><circle cx="8" cy="8" r="7"/></svg>www.velmora.ca</li>
  </ul>

  <svg class="front-footer" viewBox="0 0 690 40" preserveAspectRatio="none" aria-hidden="true">
    <polygon points="0,29 372,29 361,40 0,40" fill="var(--red)"/>
    <polygon points="407,1 690,1 690,40 368,40" fill="var(--charcoal)"/>
  </svg>
  <p class="locations">Harrow Bay NT • Linden Crossing NB</p>
</section>

<section class="card card-back" aria-label="Business card back">
  <div class="back-brand">
    <span class="brand-mark"></span>
    <span class="brand-name">Velmora Consulting</span>
  </div>

  <p class="tagline">
    <span class="lead">AS THE OWNER'S REP</span><br>
    WE AIM TO ACHIEVE YOUR INFRASTRUCTURE VISION<br>
    with OUR SPECIALIZATION &amp; EXECUTION in:
  </p>

  <span class="rule rule-top"></span>
  <p class="services">
    FUNDING Planning<span class="sep">|</span>BUSINESS Planning<br>
    INFRASTRUCTURE Planning<span class="sep">|</span>PROJECT Management
  </p>
  <span class="rule rule-bottom"></span>
  <span class="since">Since 2012</span>
</section>

</body>
</html>
```